Website Banner Redesign for Kelvra Cargo Depot

Business Name:
KELVRA CARGO DEPOT

About Us:
- We’re a proudly Australian company that designs and builds tough, reliable toolboxes for Utes, Trucks, and Campervans. Our products are made to handle harsh conditions and are trusted by tradies, off-roaders, and professional fleets across the country.

Project Goal:
- We want to refresh our homepage and category banners with bold, modern designs that better showcase our products and value proposition.

Why We’re Updating:
Our current banners show the products well, but we want to improve:
Visual impact and hierarchy
- Readability of text (especially on mobile)
- Clearer calls-to-action (CTAs)
- Brand messaging around “Built Tough”, “Aussie Made”, and “Custom Fit-Outs”

Target Audience:
- Tradespeople
- 4x4 & off-road enthusiasts
- Caravan & camping community
- Ute/Truck/Caravan dealerships
- Fleet and commercial buyers

Design Style We Want:
- Bold, confident, rugged
- Clean layout with clear focal points
- Strong product imagery (we’ll supply photos)
- Use of brand colors: Black, White, Red, Grey
- Professional, not too busy or cluttered

Banner Uses:
- Homepage hero banner
- Category landing pages

UTE TOOLBOXES - https://www.kelvracargo.com.au/aluminium-toolboxes/
Truck Boxes - https://www.kelvracargo.com.au/truck-toolboxes/
Canopies - https://www.kelvracargo.com.au/canopy/
Dog Boxes - https://www.kelvracargo.com.au/dog-boxes/
CAMPER BOXES - https://www.kelvracargo.com.au/camper-toolboxes/
Accessories - https://www.kelvracargo.com.au/accessories/

- Can be reused for desktop and mobile

Inspiration Style:
Think: 4x4 accessory brands, tough tradie gear, or clean eCommerce landing banners from premium auto suppliers.

Target Market(s)

All in Brief Above

Industry/Entity Type

Retail

Requirements
Must have
• A banner using our products only. A banner for each category, and 2 alternate banners for the home page.
Nice to have
• I have added some designs which i like..... Please take a look and take inspiration from them.

```html
<!DOCTYPE html>
<html lang="en">
<head>
<meta charset="utf-8">
<title>Premium Undertray Tool Boxes – Kelvra Cargo Depot</title>
<link rel="stylesheet" href="https://fonts.googleapis.com/css2?family=Anton&display=swap">
<style>
  :root {
    --bg-deep: #1b1834;
    --bg-mid: #262243;
    --bg-light: #322d52;
    --white: #ffffff;
    --yellow: #ffd400;
    --crimson: #a91e4a;
    --box-dark: #151515;
    --box-mid: #2b2b2b;
  }
  * { margin: 0; padding: 0; box-sizing: border-box; }
  html, body {
    width: 1200px;
    height: 469px;
    overflow: hidden;
    background: var(--bg-deep);
  }
  .banner {
    position: relative;
    width: 1200px;
    height: 469px;
    overflow: hidden;
    font-family: "Anton", "Arial Narrow", sans-serif;
  }
  .road-scene {
    position: absolute;
    inset: 0;
    background:
      linear-gradient(180deg, var(--bg-light) 0%, var(--bg-mid) 22%, var(--bg-deep) 100%);
  }
  .road-scene::after {
    content: "";
    position: absolute;
    inset: 0;
    background: radial-gradient(ellipse 35% 90% at 55% 100%, rgba(80,74,120,0.35), transparent 70%);
  }
  .headline {
    position: absolute;
    left: 149px;
    top: 70px;
    color: var(--white);
    font-size: 90px;
    line-height: 80px;
    letter-spacing: 1px;
    text-transform: uppercase;
  }
  .tagline {
    position: absolute;
    left: 149px;
    top: 318px;
    color: var(--yellow);
    font-size: 38px;
    line-height: 41px;
    text-transform: uppercase;
  }
  .product-photo {
    position: absolute;
    left: 601px;
    top: 65px;
    width: 531px;
    height: 263px;
    border-radius: 4px;
    background: linear-gradient(160deg, var(--box-mid) 0%, var(--box-dark) 55%, #0b0b0b 100%);
  }
  .cta {
    position: absolute;
    left: 820px;
    top: 342px;
    width: 206px;
    height: 48px;
    border-radius: 10px;
    background: var(--crimson);
    color: var(--white);
    font-size: 31px;
    line-height: 48px;
    text-align: center;
    text-decoration: none;
    text-transform: uppercase;
  }
</style>
</head>
<body>
  <main class="banner">
    <div class="road-scene" role="img" aria-label="Dark purple-tinted photo of an open asphalt road with a faded centre line stretching to the horizon"></div>

    <h1 class="headline">Premium<br>Undertray<br>Tool Boxes</h1>

    <p class="tagline">Maximize storage without<br>compromising space</p>

    <div class="product-photo" role="img" aria-label="Black steel undertray tool box with its slide-out drawer partly open, showing two chrome T-handle locks and drawer runners"></div>

    <a class="cta" href="https://www.kelvracargo.com.au/truck-toolboxes/">View Range</a>
  </main>
</body>
</html>
```